1876 Basins & Spouts Business Card

I'm wanting to get a business card designed. Our business is 1876 Basins & Spouts
Details for the card:

1876 Basins & Spouts
Name: Harold Vesk
Email: harold@1876basinsandspouts.com.au
Website: www.1876basinsandspouts.com.au
Mobile: 0438 260 947
Phone: 02 7481 3926

Font of Basins & Spouts is called Snell Roundhand. Not sue what font logo text is.

I'm thinking two sided but it doesn't have to be.

```html
<!DOCTYPE html>
<html lang="en">
<head>
<meta charset="utf-8">
<title>1876 Basins &amp; Spouts — Business Card</title>
<link rel="stylesheet" href="https://fonts.googleapis.com/css2?family=Lato:wght@300;400&family=Montserrat:wght@600&display=swap">
<style>
  :root {
    --ink: #1f1c1d;
    --card-dark: #231f20;
    --paper: #ffffff;
    --stage: #e9e8e6;
    --rule: #8a8788;
    --muted: #4a4647;
  }
  * { box-sizing: border-box; margin: 0; padding: 0; }
  html, body { width: 1200px; height: 912px; overflow: hidden; }
  body {
    background: var(--stage);
    font-family: "Lato", sans-serif;
    color: var(--ink);
    position: relative;
  }
  .card {
    position: absolute;
    width: 560px;
    height: 320px;
    border-radius: 16px;
    overflow: hidden;
    box-shadow: 0 10px 28px rgba(0,0,0,0.18);
  }
  .card-back {
    left: 90px; top: 100px;
    background: var(--card-dark);
    display: flex; align-items: center; justify-content: center;
  }
  .brand-back {
    color: #fff;
    font-size: 34px;
    font-weight: 300;
    letter-spacing: 1px;
    display: flex; align-items: center; gap: 14px;
  }
  .brand-dot {
    width: 14px; height: 14px; border-radius: 50%;
    border: 1.5px solid currentColor;
  }
  .card-front { left: 550px; top: 480px; background: var(--paper); }
  .wave { position: absolute; inset: 0; }
  .person {
    position: absolute; right: 30px; top: 28px; text-align: right;
  }
  .person-name {
    font-family: "Montserrat", sans-serif;
    font-weight: 600; font-size: 21px; letter-spacing: 0.5px;
  }
  .person-role { font-size: 13px; color: var(--muted); margin-top: 2px; }
  .name-rule {
    position: absolute; right: 30px; top: 84px;
    width: 270px; height: 1px; background: var(--rule);
  }
  .address {
    position: absolute; right: 30px; top: 98px;
    text-align: right; font-size: 14px; line-height: 1.35; color: var(--muted);
  }
  .brand-front {
    position: absolute; left: 30px; top: 108px;
  }
  .brand-front-name {
    font-size: 20px; font-weight: 400; color: var(--ink);
    display: flex; align-items: center; gap: 8px;
  }
  .brand-front-name .brand-dot { width: 10px; height: 10px; }
  .tagline { font-size: 8px; color: var(--muted); margin-top: 4px; margin-left: 18px; }
  .contact-rule {
    position: absolute; left: 30px; top: 196px;
    width: 270px; height: 1px; background: var(--rule);
  }
  .contacts {
    position: absolute; left: 30px; top: 208px;
    list-style: none; font-size: 15px; line-height: 23px; color: var(--ink);
  }
  .contacts li { display: flex; align-items: center; gap: 8px; }
  .contacts svg { width: 11px; height: 11px; flex: none; }
</style>
</head>
<body>

<section class="card card-back" aria-label="Card back">
  <div class="brand-back"><span class="brand-dot"></span>1876 Basins &amp; Spouts</div>
</section>

<section class="card card-front" aria-label="Card front">
  <svg class="wave" viewBox="0 0 560 320" aria-hidden="true">
    <path d="M560,150 C495,160 465,228 378,270 C330,293 290,305 240,316" fill="none" stroke="var(--card-dark)" stroke-width="1.5"/>
    <path d="M560,168 C505,176 475,244 392,284 C345,305 305,315 265,320 L560,320 Z" fill="var(--card-dark)"/>
  </svg>

  <div class="person">
    <div class="person-name">HAROLD VESK</div>
    <div class="person-role">Director</div>
  </div>
  <div class="name-rule"></div>
  <div class="address">PO Box 41 Mount<br>Kestrel NSW 2791</div>

  <div class="brand-front">
    <div class="brand-front-name"><span class="brand-dot"></span>1876 Basins &amp; Spouts</div>
    <div class="tagline">Classic fixtures shaped for the way homes live today</div>
  </div>

  <div class="contact-rule"></div>
  <ul class="contacts">
    <li><svg viewBox="0 0 12 12"><path d="M2.5 1 L4.5 1 L5 3.5 L3.8 4.5 C4.5 6 6 7.5 7.5 8.2 L8.5 7 L11 7.5 L11 9.5 C11 10.5 10 11 9 11 C4.5 10.5 1.5 7.5 1 3 C1 2 1.5 1 2.5 1 Z" fill="currentColor"/></svg>0438 260 947</li>
    <li><svg viewBox="0 0 12 12"><rect x="3" y="0.8" width="6" height="10.4" rx="1" fill="none" stroke="currentColor" stroke-width="1.2"/><circle cx="6" cy="9.4" r="0.7" fill="currentColor"/></svg>02 7481 3926</li>
    <li><svg viewBox="0 0 12 12"><rect x="0.8" y="2.5" width="10.4" height="7" fill="none" stroke="currentColor" stroke-width="1.1"/><path d="M0.8 2.5 L6 6.5 L11.2 2.5" fill="none" stroke="currentColor" stroke-width="1.1"/></svg>harold@1876basinsandspouts.com.au</li>
    <li><svg viewBox="0 0 12 12"><circle cx="6" cy="6" r="5.2" fill="currentColor"/><path d="M1 6 H11 M6 1 C3.5 3.5 3.5 8.5 6 11 M6 1 C8.5 3.5 8.5 8.5 6 11" fill="none" stroke="#fff" stroke-width="0.7"/></svg>www.1876basinsandspouts.com.au</li>
  </ul>
</section>

</body>
</html>
```